HOT TUB - SPAS service needs an business card

I need an business for my company who his specialise in a maintenance,water treatment and cleaning of Hot Tub - Spas for commercial and residential customers. The company operate mainly in the ski resort of Chamonix, Megève and St Gervais. The final product should communicate pure water, cleanest and professional for luxury property's.
I have upload a logo but any improvement on it is welcome.(color,size, details etc..) or any other idea. Thank you
Company Name: 58 BAINS
My name: Lucien Marchetti
Email: lucimarch@examplemail.net
Tel: +33 (0)6 71 58 29 64
Description to be on the card in french(first langage) and in English:
- Spas service
- Entretien, traitement eau, nettoyage.
- Maintenance, water treatment, cleaning.
Industry/Entity Type
Residential
Colors
Designer to choose colors to be used in the design.
Look and feel
Each slider illustrates characteristics of the customer's brand and the style your logo design should communicate.

```html
<!DOCTYPE html>
<html lang="fr">
<head>
<meta charset="utf-8">
<title>58 BAINS – Carte de visite</title>
<link rel="stylesheet" href="https://fonts.googleapis.com/css2?family=Open+Sans:wght@400;600;700&display=swap">
<style>
  :root {
    --page: #eef1f4;
    --card-light: #1fa3f5;
    --card-deep: #1078d8;
    --band-dark: #0c5fd0;
    --band-stripe: #8fd0fb;
    --art-light: #4db6f7;
    --art-deep: #3590e0;
    --ink: #ffffff;
    --divider: rgba(255,255,255,0.7);
  }
  * { margin: 0; padding: 0; box-sizing: border-box; }
  html, body {
    width: 1200px; height: 1055px; overflow: hidden;
    background: var(--page);
    font-family: "Open Sans", Arial, sans-serif;
    color: var(--ink);
  }
  .canvas { position: relative; width: 1200px; height: 1055px; }
  .card {
    position: absolute; width: 812px; height: 464px; overflow: hidden;
    box-shadow: 0 4px 14px rgba(0,0,0,0.18);
  }
  .card--front { left: 345px; top: 39px; background: var(--card-light); }
  .card--back  { left: 46px;  top: 538px; background: var(--card-deep); }

  .artwork { position: absolute; border-radius: 4px; }
  .card--front .artwork { left: 46px; top: 169px; width: 416px; height: 116px;
    background: linear-gradient(180deg, var(--card-light), var(--art-light)); }
  .card--back .artwork { left: 100px; top: 92px; width: 626px; height: 171px;
    background: linear-gradient(180deg, var(--card-deep), var(--art-deep)); }

  .contact {
    position: absolute; left: 506px; top: 224px; height: 61px;
    border-left: 1px solid var(--divider); padding-left: 13px;
    display: flex; flex-direction: column; justify-content: space-between;
    font-size: 18px; line-height: 24px;
  }
  .contact__row { display: flex; align-items: center; gap: 7px; white-space: nowrap; }
  .contact__icon { width: 16px; height: 16px; flex: none; }

  .holder-name {
    position: absolute; left: 44px; top: 386px;
    font-size: 27px; font-weight: 700; letter-spacing: 0.2px;
  }
  .footer-band { position: absolute; left: 0; top: 407px; width: 812px; height: 57px; }
  .company-name {
    position: absolute; left: 600px; top: 411px;
    font-size: 36px; font-weight: 700; line-height: 48px;
  }

  .services {
    position: absolute; left: 0; top: 320px; width: 100%; text-align: center;
  }
  .services__title { font-size: 27px; font-weight: 700; line-height: 40px; }
  .services__list { font-size: 26px; line-height: 37px; margin-top: 6px; }
</style>
</head>
<body>
<main class="canvas">

  <section class="card card--front" aria-label="Recto">
    <div class="artwork" role="img" aria-label="Line drawing of mountains, a chalet and a hot tub"></div>

    <div class="contact">
      <div class="contact__row">
        <svg class="contact__icon" viewBox="0 0 16 16" aria-hidden="true"><path d="M4 1.5l2.2 2.8-1.4 1.6a8 8 0 0 0 5.3 5.3l1.6-1.4 2.8 2.2-1.6 2.2C7.500 14.5 1.5 8.500 1.800 3.100z" fill="none" stroke="#fff" stroke-width="1.3"/></svg>
        <span>+33 (0)6 71 58 29 64</span>
      </div>
      <div class="contact__row">
        <svg class="contact__icon" viewBox="0 0 16 16" aria-hidden="true"><rect x="1.5" y="4" width="13" height="9" rx="1" fill="#fff"/><path d="M2 4.5l6 4.5 6-4.5" fill="none" stroke="#1fa3f5" stroke-width="1.3"/></svg>
        <span>lucimarch@examplemail.net</span>
      </div>
    </div>

    <p class="holder-name">Lucien Marchetti</p>

    <svg class="footer-band" viewBox="0 0 812 57" aria-hidden="true">
      <rect x="0" y="23" width="812" height="6" fill="var(--band-stripe)"/>
      <rect x="0" y="29" width="812" height="28" fill="var(--band-dark)"/>
      <path d="M520 29 C545 29 548 4 585 1 L812 0 L812 57 L520 57 Z" fill="var(--band-dark)"/>
    </svg>
    <p class="company-name">58 BAINS</p>
  </section>

  <section class="card card--back" aria-label="Verso">
    <div class="artwork" role="img" aria-label="Line drawing of mountains, a chalet and a hot tub"></div>
    <div class="services">
      <h2 class="services__title">SPAS SERVICES</h2>
      <p class="services__list">•Entretien &nbsp;•&nbsp;traitement eau &nbsp;•&nbsp;nettoyage<br>•Maintenance &nbsp;•&nbsp;water treatment &nbsp;•cleaning.</p>
    </div>
  </section>

</main>
</body>
</html>
```